Tollin Waste Website Design

Our new start-up needs a website design. We plan to help businesses find more sustainable ways to manage their waste. Our initial website aims to gather contact data from potential business customers and comprehensive information from waste facilities and waste transporters. We have a logo design (attached) which we would like included in the website design. I have also attached a number of pages that describe what information should appear on each page as well as a web design brief file that describes the look we are after.

```html
<!DOCTYPE html>
<html lang="en">
<head>
<meta charset="utf-8">
<title>Tollin Waste</title>
<link href="https://fonts.googleapis.com/css2?family=Montserrat:wght@500;600;700&family=Roboto:wght@400&display=swap" rel="stylesheet">
<style>
  :root {
    --green-dark: #5d9a2c;
    --green-lime: #9ccb2a;
    --text-dark: #3a3a3a;
    --footer-bg: #333333;
    --white: #ffffff;
  }
  * { margin: 0; padding: 0; box-sizing: border-box; }
  html, body { width: 1200px; height: 1112px; overflow: hidden; background: var(--white); }
  body { position: relative; font-family: "Montserrat", sans-serif; }

  .top-rule { position: absolute; left: 0; top: 0; width: 1200px; height: 4px; background: var(--green-dark); }

  .site-header { position: absolute; left: 0; top: 4px; width: 1200px; height: 100px; }
  .brand { position: absolute; left: 86px; top: 28px; display: flex; align-items: center; gap: 10px; }
  .brand-dot { width: 40px; height: 40px; border-radius: 50%; background: var(--green-lime); }
  .brand-name { font-weight: 700; font-size: 28px; color: var(--green-dark); letter-spacing: 0.5px; }

  .main-nav { position: absolute; top: 45px; right: 87px; display: flex; gap: 56px; }
  .main-nav a { font-size: 12.5px; font-weight: 600; color: var(--text-dark); text-decoration: none; text-transform: uppercase; }
  .main-nav a.is-active { color: var(--green-dark); }

  .hero { position: absolute; left: 0; top: 104px; width: 1200px; height: 553px;
    background: linear-gradient(180deg, #4f6b33 0%, #6b7f3c 30%, #b8862a 52%, #6f6a5a 75%, #4a4a48 100%); }
  .hero-tag { position: absolute; left: 86px; height: 55px; display: flex; align-items: center; padding: 0 28px;
    font-size: 22px; font-weight: 500; color: var(--white); text-transform: uppercase; white-space: nowrap; }
  .hero-tag.welcome { top: 275px; background: var(--green-lime); }
  .hero-tag.control { top: 339px; background: var(--green-dark); }

  .services { position: absolute; left: 86px; top: 699px; width: 1027px; display: flex; gap: 17px; }
  .service-card { position: relative; width: 331px; height: 288px; }
  .service-photo { position: absolute; left: 0; top: 0; width: 331px; height: 232px; }
  .service-card:nth-child(1) .service-photo { background: linear-gradient(180deg, #7fa6d6 0%, #c9d5e0 50%, #8a8d8c 100%); }
  .service-card:nth-child(2) .service-photo { background: linear-gradient(180deg, #3a7fb0 0%, #8a8478 50%, #6a5e4d 100%); }
  .service-card:nth-child(3) .service-photo { background: linear-gradient(180deg, #6e7c8a 0%, #8d8a80 55%, #5d4e3e 100%); }
  .service-band { position: absolute; left: 0; top: 232px; width: 331px; height: 56px;
    display: flex; align-items: center; justify-content: center;
    font-size: 16.5px; font-weight: 500; color: var(--white); text-transform: uppercase; }
  .service-badge { position: absolute; left: 122px; top: 188px; width: 88px; height: 44px;
    border-radius: 44px 44px 0 0;
    display: flex; align-items: flex-start; justify-content: center; padding-top: 8px; }
  .tone-dark .service-band, .tone-dark .service-badge { background: var(--green-dark); }
  .tone-lime .service-band, .tone-lime .service-badge { background: var(--green-lime); }

  .site-footer { position: absolute; left: 0; top: 1048px; width: 1200px; height: 64px; background: var(--footer-bg);
    display: flex; align-items: center; justify-content: center;
    font-family: "Roboto", sans-serif; font-size: 12.5px; color: var(--white); }
</style>
</head>
<body>
  <div class="top-rule"></div>

  <header class="site-header">
    <div class="brand">
      <span class="brand-dot"></span>
      <span class="brand-name">TOLLIN WASTE</span>
    </div>
    <nav class="main-nav">
      <a href="#" class="is-active">Home</a>
      <a href="#">About Us</a>
      <a href="#">What We Do</a>
      <a href="#">Resources</a>
      <a href="#">Contact Us</a>
    </nav>
  </header>

  <section class="hero" role="img" aria-label="Orange refuse truck lifting a metal waste container on a tree-lined street">
    <div class="hero-tag welcome">Welcome to Tollin Waste</div>
    <div class="hero-tag control">Take control of your waste here</div>
  </section>

  <section class="services">
    <article class="service-card tone-dark">
      <div class="service-photo" role="img" aria-label="Industrial plant with a tall chimney under blue sky"></div>
      <div class="service-band">Waste Producers</div>
      <div class="service-badge">
        <svg width="32" height="32" viewBox="0 0 40 40" fill="none" stroke="#fff" stroke-width="2.4" stroke-linejoin="round">
          <path d="M4 36V20l8 5v-5l8 5v-5l8 5V8h6v28z"/>
          <rect x="9" y="28" width="5" height="4"/><rect x="17" y="28" width="5" height="4"/><rect x="25" y="28" width="5" height="4"/>
        </svg>
      </div>
    </article>
    <article class="service-card tone-lime">
      <div class="service-photo" role="img" aria-label="Loader moving a compressed bale of waste paper at a facility"></div>
      <div class="service-band">Waste Facilities</div>
      <div class="service-badge">
        <svg width="32" height="32" viewBox="0 0 40 40" fill="none" stroke="#fff" stroke-width="3.5" stroke-linecap="round" stroke-linejoin="round">
          <path d="M15 10l5-6 5 6"/><path d="M20 4l7 12"/>
          <path d="M31 22l3 7-8 1"/><path d="M34 29H20"/>
          <path d="M12 31l-8-1 3-7"/><path d="M4 30l7-12"/>
        </svg>
      </div>
    </article>
    <article class="service-card tone-dark">
      <div class="service-photo" role="img" aria-label="White refuse truck beside a pile of waste under a steel shed"></div>
      <div class="service-band">Waste Transporters</div>
      <div class="service-badge">
        <svg width="35" height="32" viewBox="0 0 44 40" fill="none" stroke="#fff" stroke-width="2.4" stroke-linejoin="round">
          <path d="M4 28V16l8-4h4v16z"/><path d="M16 10h24v18H16z"/>
          <path d="M22 14v10M28 14v10M34 14v10"/>
          <circle cx="10" cy="31" r="3"/><circle cx="26" cy="31" r="3"/><circle cx="35" cy="31" r="3"/>
        </svg>
      </div>
    </article>
  </section>

  <footer class="site-footer">© Copyright -2018 Tollin Waste Management.All rights reserved.</footer>
</body>
</html>
```